Medical centre needs a business card

We are a medcial centre in Australia, needing a new business card. Our demographic is low working class families. We are going to be renovating our premises to modernise the look and also had a new logo done a few months ago representing quality and community, and now need to update our cards. It needs to be doubled sided, with logo and contact details on the front, and appointment details on the back. . Needs to be modern and simple, easy to read. <br/><br/>Name: Kindle Grove Medical Centre <br/>Address: 512 Parmley Rd (Cnr Parmley Rd & Osgood Creek Rd),<br/>Tindarra Court Shopping Centre, Paralowie, SA 5108<br/>Ph: 08 8461 3072<br/>Tag line: Where your wellbeing comes first<br/>Website: www.kindlegrovemedicalcentre-example.com.au<br/>Online bookings also available<br/><br/>(On the back, to have 3 lines of appointments that can be written in.<br/>Day, date, time)<br/><br/>Your next appointment is on<br/>Can try “M T W Th F Sa Su _________________ at ____________ am/pm” or other combinations <br/>Please advise as soon as possible if unable to attend<br/>Cancellation fees apply if less than 2 hrs notice<br/>Online appointments available (please highlight this option by either by position, colour or font)

Target Market(s)

Lower social economic working class, young families to seniors

Industry/Entity Type

Medical Centre

Contact Information for Business Card

Kindle Grove Medical Centre
512 Parmley Rd (Cnr Parmley Rd & Osgood Creek Drive)
Tindarra Court Shopping Centre
Marlowe Heights SA 5126
Ph: 08 8461 3072
www.kindlegrovemedicalcentre-example.com.au
Tagline line: where your wellbeing comes first
Back side is for appointments
Your next appointment is with Dr ______________
Day/date/time (Please give 3 lines of appointments)
Please advise as soon as possible if unable to attend
Cancellation fees apply if less than 2 hours notice
Online appointments available
Book online easily and conveniently (please highlight online appointments)

Font styles to use
Serif
Sans Serif

Colors

Designer to choose colors to be used in the design.

Requirements
Must have
• Modern and simple
• Easy to ready
• Induces a wellbeing feeling
• Incorporate our logo colours and feel from logo
• Induces feeling of stability and security
Nice to have
• Attract attention
• Pleasant to look at
• Feeling of innovation
Should not have
• Loud clashing colours
• Overly luxurious feeling
• Overly artistic

```html
<!DOCTYPE html>
<html lang="en">
<head>
<meta charset="utf-8">
<title>Kindle Grove Medical Centre – Business Card</title>
<link rel="stylesheet" href="https://fonts.googleapis.com/css2?family=Roboto+Condensed:wght@400;500&family=Work+Sans:wght@400;500;600&display=swap">
<style>
  :root {
    --page: #2b2b2b;
    --card: #ffffff;
    --blue-light: #2aa8e2;
    --blue-deep: #0a6cb8;
    --blue-text: #1466b3;
    --green: #a8d14f;
    --grey-text: #7a7a7a;
    --white: #ffffff;
  }
  * { box-sizing: border-box; margin: 0; padding: 0; }
  html, body { width: 1200px; height: 900px; overflow: hidden; }
  body { background: var(--page); position: relative; }

  .card {
    position: absolute;
    left: 261px;
    width: 656px;
    height: 358px;
    background: var(--card);
    border-radius: 30px;
    overflow: hidden;
  }
  .card--front { top: 69px; }
  .card--back { top: 472px; }

  .front-art { position: absolute; inset: 0; width: 100%; height: 100%; }

  .front-info {
    position: absolute;
    right: 27px;
    top: 0;
    text-align: right;
    color: var(--white);
    font-family: "Roboto Condensed", sans-serif;
    font-weight: 400;
    letter-spacing: 0.06em;
  }
  .brand-name {
    position: absolute;
    right: 0;
    top: 120px;
    width: 360px;
    font-weight: 500;
    line-height: 1;
    white-space: nowrap;
  }
  .brand-name__main { display: block; font-size: 34px; letter-spacing: 0.05em; }
  .brand-name__sub { display: block; font-size: 14px; letter-spacing: 0.34em; margin-top: 6px; margin-right: -0.34em; }

  .contact { position: absolute; right: 0; top: 200px; font-size: 15px; line-height: 20px; white-space: nowrap; }
  .address { position: absolute; right: 0; top: 256px; font-size: 15px; line-height: 20px; white-space: nowrap; }
  .tagline { position: absolute; right: 5px; top: 312px; font-size: 21px; letter-spacing: 0.05em; white-space: nowrap; }

  .back-inner {
    position: absolute; inset: 0;
    font-family: "Work Sans", sans-serif;
    color: var(--blue-text);
  }
  .back-brand {
    position: absolute;
    left: 0; right: 0; top: 36px;
    text-align: center;
    font-weight: 600;
    line-height: 1;
    color: var(--blue-text);
  }
  .back-brand__main { display: block; font-size: 42px; letter-spacing: 0.02em; }
  .back-brand__sub { display: block; font-size: 19px; letter-spacing: 0.34em; margin-top: 6px; margin-right: -0.34em; }

  .appointment { position: absolute; left: 97px; font-size: 17px; letter-spacing: 0.04em; white-space: nowrap; }
  .appointment--doctor { top: 134px; }
  .appointment--when { top: 176px; }
  .blank { display: inline-block; border-bottom: 1.5px solid var(--blue-text); height: 15px; vertical-align: baseline; }

  .notice {
    position: absolute; left: 97px; top: 220px;
    font-size: 15.5px; line-height: 21px; letter-spacing: 0.06em;
    color: var(--grey-text); white-space: nowrap;
  }
  .online-booking {
    position: absolute; left: 0; right: 0; top: 284px;
    text-align: center;
    font-size: 21px; line-height: 28px; font-weight: 600; letter-spacing: 0.07em;
    color: var(--blue-text);
  }
</style>
</head>
<body>

  <section class="card card--front" aria-label="Business card front">
    <svg class="front-art" viewBox="0 0 656 358" aria-hidden="true">
      <defs>
        <linearGradient id="panel-blue" x1="0" y1="0" x2="1" y2="0">
          <stop offset="0" stop-color="var(--blue-light)"/>
          <stop offset="1" stop-color="var(--blue-deep)"/>
        </linearGradient>
      </defs>
      <path class="accent-band" d="M555,0 C360,40 190,170 146,358 L192,358 C210,170 370,40 590,0 Z" fill="var(--green)"/>
      <path class="info-panel" d="M582,0 C385,45 215,175 205,358 L656,358 L656,0 Z" fill="url(#panel-blue)"/>
    </svg>

    <div class="front-info">
      <div class="brand-name">
        <span class="brand-name__main">KINDLE GROVE</span>
        <span class="brand-name__sub">MEDICAL CENTRE</span>
      </div>
      <p class="contact">08 8461 3072<br>www.kindlegrovemedicalcentre-example.com.au</p>
      <p class="address">512 Parmley Rd (Cnr Parmley Rd &amp; Osgood Creek Drive)<br>Tindarra Court Shopping Centre Marlowe Heights SA 5126</p>
      <p class="tagline">Where your wellbeing comes first</p>
    </div>
  </section>

  <section class="card card--back" aria-label="Business card back">
    <div class="back-inner">
      <div class="back-brand">
        <span class="back-brand__main">KINDLE GROVE</span>
        <span class="back-brand__sub">MEDICAL CENTRE</span>
      </div>

      <p class="appointment appointment--doctor">Your next appointment is with Dr <span class="blank" style="width:148px"></span></p>
      <p class="appointment appointment--when">Day <span class="blank" style="width:118px"></span>Date <span class="blank" style="width:108px"></span>Time <span class="blank" style="width:88px"></span></p>

      <p class="notice">Please advise as soon as possible if unable to attend<br>Cancellation fees apply if less than 2 hours notice</p>

      <p class="online-booking">Book Online Easily Conveniently<br>Online Appointments Available.</p>
    </div>
  </section>

</body>
</html>
```